Business Card Design

WE are looking for a premium quality Business Cards for a Law Firm . Copies of our current business card is attached.

Contact Information for Business Card

xyz

```html
<!DOCTYPE html>
<html lang="en">
<head>
<meta charset="utf-8">
<title>Harrowgate Lawyers – Business Cards</title>
<link href="https://fonts.googleapis.com/css2?family=Tinos:wght@400;700&display=swap" rel="stylesheet">
<style>
  :root {
    --backdrop: #232323;
    --gold: #cdab6a;
    --forest: #0f2a1e;
    --ink: #151515;
    --paper: #ffffff;
    --cream: #fffaf0;
  }
  * { box-sizing: border-box; margin: 0; padding: 0; }
  html, body { width: 1200px; height: 780px; overflow: hidden; }
  body {
    background: var(--backdrop);
    font-family: "Tinos", "Times New Roman", serif;
    position: relative;
  }
  .card {
    position: absolute;
    width: 600px;
    height: 343px;
    box-shadow: 0 10px 24px rgba(0,0,0,.55);
    overflow: hidden;
  }

  /* ---------- Offices side ---------- */
  .card--offices { left: 90px; top: 28px; background: var(--gold); }
  .brand {
    display: flex; align-items: center; gap: 10px;
    font-weight: 700; letter-spacing: 2px;
  }
  .brand__dot { border-radius: 50%; flex: none; }
  .card--offices .brand {
    position: absolute; top: 66px; left: 0; right: 0; justify-content: center;
    color: var(--forest); font-size: 30px;
  }
  .card--offices .brand__dot { width: 44px; height: 44px; border: 3px solid var(--forest); }
  .tagline {
    position: absolute; top: 158px; left: 0; right: 0; height: 26px;
    background: var(--forest); color: var(--cream);
    font-weight: 700; font-size: 14px; letter-spacing: 1px;
    display: flex; align-items: center; justify-content: center;
  }
  .offices {
    position: absolute; top: 202px; left: 0; right: 0; bottom: 20px;
    display: grid; grid-template-columns: repeat(3, 1fr);
  }
  .office {
    text-align: center; color: var(--cream);
    font-weight: 700; font-size: 11.5px; line-height: 1.45;
    position: relative; padding: 0 10px;
  }
  .office + .office::before {
    content: ""; position: absolute; left: 0; top: -8px; bottom: 4px;
    width: 1px; background: var(--cream); transform: skewX(-22deg); opacity: .85;
  }
  .office__city {
    display: inline-block; color: var(--forest); font-size: 15px;
    border-bottom: 1.5px solid var(--forest); margin-bottom: 5px; letter-spacing: 1px;
  }
  .office__phone { display: inline-flex; align-items: center; gap: 5px; margin-top: 2px; }
  .icon { width: 12px; height: 12px; flex: none; }

  /* ---------- Person side ---------- */
  .card--person { left: 510px; top: 412px; background: var(--paper); }
  .card--person .brand {
    position: absolute; left: 36px; top: 130px; flex-direction: column; gap: 8px;
    color: var(--forest); font-size: 32px; text-align: center; line-height: 1.05;
  }
  .card--person .brand__dot { width: 78px; height: 78px; border: 5px solid var(--gold); }
  .gold-tab {
    position: absolute; right: 0; top: 22px; width: 22px; height: 74px; background: var(--gold);
  }
  .person {
    position: absolute; right: 34px; top: 22px; text-align: right; color: var(--ink);
  }
  .person__name { color: var(--gold); font-weight: 700; font-size: 34px; letter-spacing: 1px; line-height: 1; }
  .person__role { font-weight: 700; font-size: 13px; line-height: 1.3; margin-top: 4px; }
  .address {
    position: absolute; right: 34px; top: 138px; text-align: right; font-style: normal;
    font-weight: 700; font-size: 13px; line-height: 1.35; color: var(--ink);
  }
  .contacts {
    position: absolute; right: 14px; top: 212px; list-style: none;
    font-weight: 700; font-size: 13px; line-height: 1.55; color: var(--ink);
  }
  .contacts li { display: flex; justify-content: flex-end; align-items: center; gap: 8px; }
  .contacts .icon { width: 13px; height: 13px; }
</style>
</head>
<body>

<section class="card card--offices">
  <div class="brand"><span class="brand__dot"></span>HARROWGATE LAWYERS</div>
  <div class="tagline">CLEAR ADVICE. STRONG OUTCOMES. ALWAYS</div>
  <div class="offices">
    <div class="office">
      <div class="office__city">MELBOURNE</div><br>
      Level 12, 48 Ardent Street,<br>MELBOURNE, VIC 3000<br>
      <span class="office__phone">
        <svg class="icon" viewBox="0 0 24 24"><path fill="#0f2a1e" d="M6.6 10.8a15 15 0 0 0 6.6 6.6l2.2-2.2c.3-.3.7-.4 1-.2 1.1.4 2.3.6 3.6.6.6 0 1 .4 1 1V20c0 .6-.4 1-1 1A17 17 0 0 1 3 4c0-.6.4-1 1-1h3.5c.6 0 1 .4 1 1 0 1.3.2 2.5.6 3.6.1.3 0 .7-.2 1z"/></svg>
        +61 03 9000 1184</span>
    </div>
    <div class="office">
      <div class="office__city">SYDNEY</div><br>
      Level 9, Corbel House<br>22 Linden Street<br>PARRAMATTA, NSW 2150<br>
      <span class="office__phone">
        <svg class="icon" viewBox="0 0 24 24"><path fill="#0f2a1e" d="M6.6 10.8a15 15 0 0 0 6.6 6.6l2.2-2.2c.3-.3.7-.4 1-.2 1.1.4 2.3.6 3.6.6.6 0 1 .4 1 1V20c0 .6-.4 1-1 1A17 17 0 0 1 3 4c0-.6.4-1 1-1h3.5c.6 0 1 .4 1 1 0 1.3.2 2.5.6 3.6.1.3 0 .7-.2 1z"/></svg>
        +61 02 9000 3371</span>
    </div>
    <div class="office">
      <div class="office__city">PERTH</div><br>
      Level 6, Orrin Tower<br>75 Halden Terrace<br>PERTH, WA 6000<br>
      <span class="office__phone">
        <svg class="icon" viewBox="0 0 24 24"><path fill="#0f2a1e" d="M6.6 10.8a15 15 0 0 0 6.6 6.6l2.2-2.2c.3-.3.7-.4 1-.2 1.1.4 2.3.6 3.6.6.6 0 1 .4 1 1V20c0 .6-.4 1-1 1A17 17 0 0 1 3 4c0-.6.4-1 1-1h3.5c.6 0 1 .4 1 1 0 1.3.2 2.5.6 3.6.1.3 0 .7-.2 1z"/></svg>
        +61 08 9000 5528</span>
    </div>
  </div>
</section>

<section class="card card--person">
  <div class="brand"><span class="brand__dot"></span>HARROWGATE<br>LAWYERS</div>
  <div class="gold-tab"></div>
  <div class="person">
    <div class="person__name">DANIEL MERCER</div>
    <div class="person__role">Director and Principal Solicitor<br>MBA, Juris Doctor</div>
  </div>
  <address class="address">
    Suite 310, Carrow Chambers,<br>215 Fenwick Street,<br>Melbourne VIC 3000
  </address>
  <ul class="contacts">
    <li>+61 7 3000 4417
      <svg class="icon" viewBox="0 0 24 24"><path fill="#cdab6a" d="M6.6 10.8a15 15 0 0 0 6.6 6.6l2.2-2.2c.3-.3.7-.4 1-.2 1.1.4 2.3.6 3.6.6.6 0 1 .4 1 1V20c0 .6-.4 1-1 1A17 17 0 0 1 3 4c0-.6.4-1 1-1h3.5c.6 0 1 .4 1 1 0 1.3.2 2.5.6 3.6.1.3 0 .7-.2 1z"/></svg></li>
    <li>+61 0400 123 456
      <svg class="icon" viewBox="0 0 24 24"><rect x="6" y="2" width="12" height="20" rx="2" fill="none" stroke="#cdab6a" stroke-width="2"/><circle cx="12" cy="18" r="1.2" fill="#cdab6a"/></svg></li>
    <li>www.harrowgatelawyers.com.au
      <svg class="icon" viewBox="0 0 24 24"><circle cx="12" cy="12" r="9" fill="none" stroke="#cdab6a" stroke-width="2"/><path d="M3 12h18M12 3c3 3 3 15 0 18M12 3c-3 3-3 15 0 18" fill="none" stroke="#cdab6a" stroke-width="1.5"/></svg></li>
    <li>daniel@harrowgatelawyers.com.au
      <svg class="icon" viewBox="0 0 24 24"><rect x="2" y="5" width="20" height="14" rx="1" fill="none" stroke="#cdab6a" stroke-width="2"/><path d="M2 6l10 7 10-7" fill="none" stroke="#cdab6a" stroke-width="2"/></svg></li>
  </ul>
</section>

</body>
</html>
```